Machining Business Order Thank You Insert

I am looking for a business style card to include with orders that I ship. The card needs to thank the recipient for their order, and encourage them to leave a review. The card should include my business name and contact information and have an area to hand write a message.

I mainly sale on Craftlane and my own website. We are a machining an manufacturing business that are in the sale of mostly metal machined and 3d printed plastic products.

The front of the card should include the following:
Logo: (attached)
Snapgram: https://www.snapgram.example/kelvomill/
Friendsbook: https://www.friendsbook.example/KelvoMill
Website: https://www.kelvomill.example/

The back of the card needs an area to write a message

Industry/Entity Type

3D Printing, Machining, Craftlane

Contact Information for Business Card

Black or white front, white back to write a personal message

Font styles to use
Sans Serif

Colors

Designer to choose colors to be used in the design.

Requirements
Must have
• Encourage a review, social media info

```html
<!DOCTYPE html>
<html lang="en">
<head>
<meta charset="utf-8">
<title>KelvoMill Order Thank You Card</title>
<link rel="stylesheet" href="https://fonts.googleapis.com/css2?family=Rubik:wght@400;500;700&display=swap">
<style>
  :root {
    --page: #cbcbcb;
    --card-dark: #141414;
    --card-mid: #262626;
    --card-white: #ffffff;
    --accent: #e8561f;
    --text-light: #f2f2f2;
    --text-dark: #1c1c1c;
    --text-muted: #6f6f6f;
    --rule: #c9c9c9;
  }
  * { box-sizing: border-box; margin: 0; padding: 0; }
  html, body { width: 1200px; height: 900px; overflow: hidden; }
  body {
    background: var(--page);
    font-family: "Rubik", sans-serif;
    position: relative;
  }
  .card {
    position: absolute;
    left: 250px;
    width: 700px;
    height: 400px;
    border: 6px solid var(--accent);
    overflow: hidden;
  }
  .card--front {
    top: 40px;
    background:
      repeating-linear-gradient(100deg, rgba(255,255,255,0.025) 0 1px, transparent 1px 3px),
      linear-gradient(135deg, var(--card-dark) 0%, var(--card-mid) 55%, var(--card-dark) 100%);
  }
  .card--back {
    top: 470px;
    background: var(--card-white);
  }

  .brand {
    position: absolute;
    display: flex;
    align-items: center;
    gap: 12px;
    color: var(--accent);
    font-weight: 500;
    letter-spacing: 0.3em;
  }
  .brand__square { width: 14px; height: 14px; background: var(--accent); }
  .card--front .brand { left: 56px; top: 250px; font-size: 24px; }
  .card--back .brand { right: 40px; bottom: 30px; font-size: 20px; }
  .card--back .brand__square { width: 11px; height: 11px; }

  .divider {
    position: absolute;
    left: 300px; top: 70px;
    width: 2px; height: 270px;
    background: linear-gradient(to bottom, transparent, var(--accent) 25%, var(--accent) 75%, transparent);
  }

  .details { position: absolute; left: 332px; top: 62px; }
  .details__name {
    color: var(--accent);
    font-weight: 700;
    font-size: 26px;
    letter-spacing: 0.02em;
    text-transform: uppercase;
  }
  .details__title { color: var(--text-light); font-size: 15px; margin-top: 2px; }
  .contact-list { list-style: none; margin-top: 22px; }
  .contact-list li {
    display: flex; align-items: center; gap: 10px;
    color: var(--text-light);
    font-size: 15px;
    height: 30px;
    white-space: nowrap;
  }
  .contact-icon { width: 20px; height: 20px; flex: none; }

  .thanks { position: absolute; left: 40px; top: 30px; right: 40px; }
  .thanks__heading {
    color: var(--accent);
    font-weight: 700;
    font-size: 26px;
    text-transform: uppercase;
    letter-spacing: 0.02em;
  }
  .thanks__note { color: var(--text-dark); font-size: 15px; margin-top: 4px; }

  .message-area {
    position: absolute;
    left: 40px; right: 40px; top: 112px;
    display: flex; flex-direction: column; gap: 38px;
  }
  .message-area__line { height: 1px; background: var(--rule); }

  .review {
    position: absolute;
    left: 40px; bottom: 28px;
    display: flex; align-items: center; gap: 10px;
    color: var(--text-dark);
    font-size: 14px;
  }
  .review strong { color: var(--accent); font-weight: 500; }
</style>
</head>
<body>

<section class="card card--front">
  <div class="brand"><span class="brand__square"></span>KELVOMILL</div>
  <div class="divider"></div>
  <div class="details">
    <p class="details__name">Marcus Hale</p>
    <p class="details__title">Managing Director</p>
    <ul class="contact-list">
      <li>
        <svg class="contact-icon" viewBox="0 0 20 20"><rect width="20" height="20" rx="4" fill="#e8561f"/><path d="M10 4a4 4 0 0 0-4 4c0 3 4 8 4 8s4-5 4-8a4 4 0 0 0-4-4z" fill="#141414"/><circle cx="10" cy="8" r="1.5" fill="#e8561f"/></svg>
        Ashford, OH
      </li>
      <li>
        <svg class="contact-icon" viewBox="0 0 20 20"><rect width="20" height="20" rx="4" fill="#e8561f"/><path d="M6 4h3l1 3-2 1.5a8 8 0 0 0 3.5 3.5L13 10l3 1v3a2 2 0 0 1-2 2A10 10 0 0 1 4 6a2 2 0 0 1 2-2z" fill="#141414"/></svg>
        000-000-0000
      </li>
      <li>
        <svg class="contact-icon" viewBox="0 0 20 20"><rect width="20" height="20" rx="4" fill="#e8561f"/><rect x="4" y="6" width="12" height="8" fill="#141414"/><path d="M4 6l6 5 6-5" stroke="#e8561f" stroke-width="1.2" fill="none"/></svg>
        info@kelvomill.example
      </li>
      <li>
        <svg class="contact-icon" viewBox="0 0 20 20"><rect width="20" height="20" rx="4" fill="#e8561f"/><circle cx="10" cy="10" r="6" fill="none" stroke="#141414" stroke-width="1.5"/><ellipse cx="10" cy="10" rx="2.5" ry="6" fill="none" stroke="#141414" stroke-width="1.2"/><path d="M4 10h12" stroke="#141414" stroke-width="1.2"/></svg>
        www.kelvomill.example
      </li>
      <li>
        <svg class="contact-icon" viewBox="0 0 20 20"><rect width="20" height="20" rx="4" fill="#e8561f"/><path d="M8.5 11.5l3-3M9 6.5l1.5-1.5a2.8 2.8 0 0 1 4 4L13 10.5M11 13.5l-1.5 1.5a2.8 2.8 0 0 1-4-4L7 9.5" stroke="#141414" stroke-width="1.6" fill="none" stroke-linecap="round"/></svg>
        https://www.snapgram.example/kelvomill/
      </li>
      <li>
        <svg class="contact-icon" viewBox="0 0 20 20"><rect width="20" height="20" rx="4" fill="#e8561f"/><path d="M8.5 11.5l3-3M9 6.5l1.5-1.5a2.8 2.8 0 0 1 4 4L13 10.5M11 13.5l-1.5 1.5a2.8 2.8 0 0 1-4-4L7 9.5" stroke="#141414" stroke-width="1.6" fill="none" stroke-linecap="round"/></svg>
        https://www.friendsbook.example/KelvoMill
      </li>
    </ul>
  </div>
</section>

<section class="card card--back">
  <div class="thanks">
    <p class="thanks__heading">Thank you for your order!</p>
    <p class="thanks__note">A personal note from our shop:</p>
  </div>
  <div class="message-area" aria-label="Space for a handwritten message">
    <div class="message-area__line"></div>
    <div class="message-area__line"></div>
    <div class="message-area__line"></div>
    <div class="message-area__line"></div>
  </div>
  <p class="review">
    <svg class="contact-icon" viewBox="0 0 20 20"><rect width="20" height="20" rx="4" fill="#e8561f"/><path d="M10 3.5l1.9 4 4.3.5-3.2 3 .9 4.3L10 13.2l-3.9 2.1.9-4.3-3.2-3 4.3-.5z" fill="#ffffff"/></svg>
    Enjoying it? <strong>Please leave us a review on Craftlane!</strong>
  </p>
  <div class="brand"><span class="brand__square"></span>KELVOMILL</div>
</section>

</body>
</html>
```